Falkrin homes and renovations business card design.

Would like some new card designs utilizing my new logo that look professional. I am open to different colors on the logo or utilize the same ones we have. I like the original concept but would like to see some fresh ideas and build on what we have already done.

Target Market(s)

Custom home building industry, Real estate sales, Renovation projects.

Industry/Entity Type

Home Builder

Contact Information for Business Card

Falkrin Homes and Renovations
2871 96th Avenue
Kestrel Falls, Norland
T2R3W8
Home : 403- 718-4063 Cell: 403- 294-5170

My info is : Dax Falkrin, President and CEO
email: falkrinhomes@maildrop-example.net
Website: falkrinhomes-example.com
websit

Requirements
Must have
• Must Use my new logo design. I am open to different colors on the logo or utilize the same ones in the existing design. I can upload the original logo design if needed.

```html
<!DOCTYPE html>
<html lang="en">
<head>
<meta charset="utf-8">
<title>Falkrin Homes and Renovations – Business Card</title>
<link rel="stylesheet" href="https://fonts.googleapis.com/css2?family=Montserrat:wght@400;500;600&display=swap">
<style>
  :root {
    --bg: #2a1a12;
    --card: #231f20;
    --gold: #b88a35;
    --yellow: #f5b80a;
    --grey: #b5b5b5;
    --white: #f2f2f2;
  }
  * { margin: 0; padding: 0; box-sizing: border-box; }
  html, body { width: 1200px; height: 750px; overflow: hidden; background: var(--bg); }
  body { position: relative; font-family: "Montserrat", sans-serif; }

  .card {
    position: absolute;
    top: 214px;
    width: 492px;
    height: 280px;
    background: var(--card);
    box-shadow: 0 4px 10px rgba(0,0,0,.55);
  }
  .card--front { left: 90px; }
  .card--back { left: 632px; }

  .brand {
    position: absolute;
    left: 0; right: 0;
    text-align: center;
    font-weight: 500;
    line-height: 1;
  }
  .brand__square {
    display: block;
    margin: 0 auto;
    background: var(--gold);
  }
  .brand__name { display: block; color: var(--gold); letter-spacing: .5px; }
  .brand__tag { display: block; color: var(--grey); letter-spacing: .6px; }

  .card--front .brand { top: 46px; }
  .card--front .brand__square { width: 14px; height: 14px; margin-bottom: 28px; }
  .card--front .brand__name { font-size: 42px; }
  .card--front .brand__tag { font-size: 13px; margin-top: 4px; }

  .card--back .brand { top: 100px; }
  .card--back .brand__square { width: 18px; height: 18px; margin-bottom: 30px; }
  .card--back .brand__name { font-size: 52px; }
  .card--back .brand__tag { font-size: 16.5px; margin-top: 4px; }

  .person {
    position: absolute;
    right: 260px;
    top: 194px;
    text-align: right;
  }
  .person__name {
    color: var(--yellow);
    font-weight: 600;
    font-size: 29px;
    line-height: 1.05;
  }
  .person__title {
    color: var(--white);
    font-size: 12.5px;
    margin-top: 2px;
  }

  .divider {
    position: absolute;
    left: 264px;
    top: 176px;
    width: 1px;
    height: 86px;
    background: var(--gold);
  }

  .contact {
    position: absolute;
    left: 296px;
    top: 175px;
    color: var(--white);
    font-size: 9.4px;
    line-height: 11.4px;
  }
  .contact__address { margin-bottom: 7px; }
  .contact__line { display: flex; align-items: center; gap: 3px; }
  .contact__line svg { width: 7px; height: 7px; fill: var(--white); flex: none; }
</style>
</head>
<body>

<section class="card card--front" aria-label="Card front">
  <div class="brand">
    <span class="brand__square"></span>
    <span class="brand__name">FALKRIN</span>
    <span class="brand__tag">HOMES AND RENOVATIONS</span>
  </div>

  <div class="person">
    <p class="person__name">Dax Falkrin</p>
    <p class="person__title">President and CEO</p>
  </div>

  <div class="divider"></div>

  <div class="contact">
    <p class="contact__address">2871 96th Avenue<br>Kestrel Falls, Norland<br>T2R3W8</p>
    <p class="contact__line">
      <svg viewBox="0 0 10 10"><rect x="2.5" y="0" width="5" height="10" rx="1"/><rect x="3.5" y="1.2" width="3" height="6.5" fill="#231f20"/></svg>
      403- 718-4063
    </p>
    <p class="contact__line">
      <svg viewBox="0 0 10 10"><path d="M0 4 Q5 0 10 4 L9 5.5 L7 4.5 L7 3.5 Q5 2.8 3 3.5 L3 4.5 L1 5.5Z"/><rect x="2" y="5.5" width="6" height="4" rx="1"/></svg>
      403- 294-5170
    </p>
    <p class="contact__line">
      <svg viewBox="0 0 10 10"><rect x="0" y="2" width="10" height="6.5"/><path d="M0 2 L5 6 L10 2" fill="none" stroke="#231f20" stroke-width="1"/></svg>
      falkrinhomes@maildrop-example.net
    </p>
    <p class="contact__line">
      <svg viewBox="0 0 10 10"><circle cx="5" cy="5" r="4.5"/><path d="M0.5 5 H9.5 M5 0.5 V9.5" stroke="#231f20" stroke-width=".8"/></svg>
      falkrinhomes-example.com
    </p>
  </div>
</section>

<section class="card card--back" aria-label="Card back">
  <div class="brand">
    <span class="brand__square"></span>
    <span class="brand__name">FALKRIN</span>
    <span class="brand__tag">HOMES AND RENOVATIONS</span>
  </div>
</section>

</body>
</html>
```